Business Card Design

We need a business card designed for our new company. Prefer a black card with white logo & writing.

Contact Information for Business Card

Ted Galloway, address: 7-4812 Fernhollow Road, Abbotsford, BC, V3K 8R2, Office Phone: 604-712-3390, Cell: 604-947-2164, Email: ted@resinworkshub.ca

Colors

Designer to choose only greyscale colors for use in the design.

```html
<!DOCTYPE html>
<html lang="en">
<head>
<meta charset="utf-8">
<title>Resin Works Hub — Business Card</title>
<link rel="stylesheet" href="https://fonts.googleapis.com/css2?family=Montserrat:wght@400;700&display=swap">
<style>
  :root {
    --backdrop: #2a2a2a;
    --card: #141414;
    --ink: #ffffff;
    --ink-muted: #f0f0f0;
    --emboss: #3a3a3a;
    --shadow: rgba(0, 0, 0, 0.55);
  }
  * { box-sizing: border-box; margin: 0; padding: 0; }
  html, body {
    width: 1200px;
    height: 1059px;
    overflow: hidden;
    background: var(--backdrop);
    font-family: "Montserrat", Arial, sans-serif;
    color: var(--ink);
  }
  .canvas { position: relative; width: 1200px; height: 1059px; }

  .card {
    position: absolute;
    background: var(--card);
    border-radius: 20px;
    box-shadow: 0 10px 24px var(--shadow);
  }
  .card--front { left: 256px; top: 89px; width: 688px; height: 390px; }
  .card--back  { left: 253px; top: 546px; width: 694px; height: 392px; }

  .wordmark {
    position: absolute;
    left: 0; right: 0;
    display: flex;
    align-items: center;
    justify-content: center;
    gap: 14px;
    font-weight: 700;
    letter-spacing: 0.5px;
    white-space: nowrap;
  }
  .wordmark__mark {
    width: 26px; height: 26px;
    border-radius: 50%;
  }
  .card--front .wordmark { top: 165px; font-size: 50px; color: var(--emboss); }
  .card--front .wordmark__mark { background: var(--emboss); width: 34px; height: 34px; }
  .card--back .wordmark { top: 92px; font-size: 34px; color: var(--ink); }
  .card--back .wordmark__mark { background: var(--ink); }

  .person {
    position: absolute;
    right: 368px;
    top: 240px;
    text-align: right;
  }
  .person__name { font-size: 28px; font-weight: 700; line-height: 1.1; }
  .person__role { font-size: 18px; font-weight: 400; margin-top: 8px; color: var(--ink-muted); }

  .divider {
    position: absolute;
    left: 352px; top: 245px;
    width: 2px; height: 73px;
    background: var(--ink);
  }

  .contacts {
    position: absolute;
    left: 376px; top: 242px;
    list-style: none;
    font-size: 18px;
    line-height: 27px;
  }
  .contacts li { display: flex; align-items: center; gap: 8px; }
  .contacts svg { width: 14px; height: 14px; fill: var(--ink); flex: none; }

  .address {
    position: absolute;
    left: 0; right: 0; top: 340px;
    text-align: center;
    font-size: 18px;
  }
</style>
</head>
<body>
<main class="canvas">
  <section class="card card--front" aria-label="Card front">
    <div class="wordmark"><span class="wordmark__mark"></span>RESIN WORKS HUB</div>
  </section>

  <section class="card card--back" aria-label="Card back">
    <div class="wordmark"><span class="wordmark__mark"></span>RESIN WORKS HUB</div>

    <div class="person">
      <p class="person__name">Ted Galloway</p>
      <p class="person__role">Owner/CEO</p>
    </div>

    <span class="divider"></span>

    <ul class="contacts">
      <li>
        <svg viewBox="0 0 16 16" aria-hidden="true"><path d="M2 6c0-2 2-3 6-3s6 1 6 3v1h-3V5.5H5V7H2z M4 8h8l1 5H3z"/></svg>
        604-712-3390
      </li>
      <li>
        <svg viewBox="0 0 16 16" aria-hidden="true"><path d="M4.5 1h7a1 1 0 0 1 1 1v12a1 1 0 0 1-1 1h-7a1 1 0 0 1-1-1V2a1 1 0 0 1 1-1zm.5 2v9h6V3zm3 9.7a.7.7 0 1 0 0 1.4.7.7 0 0 0 0-1.4z"/></svg>
        604-947-2164
      </li>
      <li>
        <svg viewBox="0 0 16 16" aria-hidden="true"><path d="M1 6l7-4 7 4v8H1zm1.5 1.2V12.5l3.6-3zm11 0L9.9 9.5l3.6 3zM3 13.5h10L8.7 10h-1.4z"/></svg>
        ted@resinworkshub.ca
      </li>
    </ul>

    <p class="address">7-4812 Fernhollow Road, Abbotsford, BC, V3K 8R2</p>
  </section>
</main>
</body>
</html>
```